Boutique custom software development company needs new business card

Our nearly 20 year old custom software development company would like to better include the fact that we are now providing Bitcoin services. These new services are B2B include education (how to acquire and securely hold Bitcoin) and integrating Bitcoin payments into existing ecommerce sites or other existing systems. Please keep the card clean and simple. Attached is our current design and some other files. vextorial.com

Target Market(s)

businesses owners interested in long term relationship

Industry/Entity Type

Custom software development and Bitcoin

Contact Information for Business Card

Dale Parker, dale@vextorial.com, vextorial.com, (888) 555-VXTRL

Font styles to use
Other font styles liked:
• monospace

Requirements
Must have
• double-sided
Nice to have
• clean and simple
Should not have
• physical address

```html
<!DOCTYPE html>
<html lang="en">
<head>
<meta charset="utf-8">
<title>Vextorial Business Card</title>
<link href="https://fonts.googleapis.com/css2?family=Poppins:wght@400;700&family=Lato:wght@400&family=Rubik:wght@700&display=swap" rel="stylesheet">
<style>
  :root {
    --backdrop: #1b1b1b;
    --card-white: #ffffff;
    --brand-blue: #3f72b7;
    --brand-orange: #ef7a22;
    --text-dark: #333333;
    --shadow: rgba(0,0,0,0.9);
  }
  * { margin: 0; padding: 0; box-sizing: border-box; }
  html, body {
    width: 1075px; height: 1200px; overflow: hidden;
    background: var(--backdrop);
  }
  .canvas { position: relative; width: 1075px; height: 1200px; }
  .card {
    position: absolute;
    width: 660px; height: 393px;
    border-radius: 28px;
    box-shadow: 4px 4px 3px var(--shadow);
    overflow: hidden;
  }
  .card--front { left: 209px; top: 188px; background: var(--card-white); }
  .card--back { left: 206px; top: 637px; background: var(--brand-blue); }

  .wordmark {
    position: absolute;
    font-family: "Poppins", sans-serif;
    font-weight: 700;
    line-height: 1;
    letter-spacing: -0.5px;
  }
  .tagline {
    position: absolute;
    font-family: "Lato", sans-serif;
    line-height: 1;
    letter-spacing: -0.6px;
    white-space: nowrap;
  }
  .card--front .wordmark {
    right: 43px; top: 76px;
    font-size: 41px; color: var(--brand-blue);
  }
  .card--front .tagline {
    right: 50px; top: 129px;
    font-size: 17px; color: var(--brand-blue);
  }

  .holder-name {
    position: absolute; left: 38px; top: 203px;
    font-family: "Rubik", sans-serif; font-weight: 700;
    font-size: 28px; line-height: 1; letter-spacing: -0.3px;
    white-space: nowrap;
  }
  .holder-name .first { color: var(--brand-orange); }
  .holder-name .last { color: var(--brand-blue); }
  .divider {
    position: absolute; left: 38px; top: 241px; width: 579px;
    height: 1.5px; background: var(--brand-blue);
  }
  .contact-list { position: absolute; left: 38px; top: 263px; list-style: none; }
  .contact-list li {
    display: flex; align-items: center; gap: 8px;
    height: 29.5px;
    font-family: "Poppins", sans-serif; font-size: 19px; color: var(--text-dark);
    white-space: nowrap;
  }
  .contact-list svg { width: 25px; height: 25px; flex: none; }
  .contact-list .accent { color: var(--brand-blue); }

  .card--back .wordmark {
    left: 0; right: 0; text-align: center; top: 145px;
    font-size: 62px; color: var(--card-white);
  }
  .card--back .tagline {
    left: 0; right: 0; text-align: center; top: 220px;
    font-size: 25px; color: var(--card-white);
  }
  .services {
    position: absolute; left: 0; right: 0; bottom: 42px;
    text-align: center;
    font-family: "Poppins", sans-serif; font-size: 15px; line-height: 1;
    letter-spacing: 1px; color: var(--card-white);
    white-space: nowrap;
  }
  .services .dot { color: var(--brand-orange); padding: 0 8px; }
</style>
</head>
<body>
<div class="canvas">
  <section class="card card--front">
    <div class="wordmark">VEXTORIAL</div>
    <div class="tagline">developer of custom applications</div>
    <div class="holder-name"><span class="first">DALE</span> <span class="last">PARKER</span></div>
    <div class="divider"></div>
    <ul class="contact-list">
      <li>
        <svg viewBox="0 0 25 25" aria-hidden="true"><rect width="25" height="25" rx="3" fill="#ef7a22"/><path d="M8 6.5c-1.5 1-1.8 2.8-.6 5.2 1.4 2.8 3.6 5 6.4 6.4 2.4 1.2 4.2.9 5.2-.6l-2.4-2.3-1.8 1c-1.7-.8-3.6-2.7-4.4-4.4l1-1.8z" fill="none" stroke="#fff" stroke-width="1.5" stroke-linejoin="round"/><path d="M14 6.5a4.5 4.5 0 0 1 4.5 4.5M14 9a2 2 0 0 1 2 2" fill="none" stroke="#fff" stroke-width="1.3" stroke-linecap="round"/></svg>
        <span>(888) 555-VXTRL</span>
      </li>
      <li>
        <svg viewBox="0 0 25 25" aria-hidden="true"><rect width="25" height="25" rx="3" fill="#ef7a22"/><rect x="5" y="7.5" width="15" height="10" fill="none" stroke="#fff" stroke-width="1.5"/><path d="M5 7.5l7.5 6 7.5-6M5 17.5l5.5-5M20 17.5l-5.5-5" fill="none" stroke="#fff" stroke-width="1.3"/></svg>
        <span>dale@vextorial.com</span>
      </li>
      <li>
        <svg viewBox="0 0 25 25" aria-hidden="true"><rect width="25" height="25" rx="3" fill="#ef7a22"/><circle cx="12.5" cy="12.5" r="7" fill="none" stroke="#fff" stroke-width="1.4"/><ellipse cx="12.5" cy="12.5" rx="3" ry="7" fill="none" stroke="#fff" stroke-width="1.2"/><path d="M5.5 12.5h14M6.5 9h12M6.5 16h12" stroke="#fff" stroke-width="1.1"/></svg>
        <span>www.<span class="accent">vextorial</span>.com</span>
      </li>
    </ul>
  </section>

  <section class="card card--back">
    <div class="wordmark">VEXTORIAL</div>
    <div class="tagline">developer of custom applications</div>
    <div class="services">CUSTOM SOFTWARE<span class="dot">•</span>BITCOIN EDUCATION<span class="dot">•</span>BITCOIN PAYMENTS</div>
  </section>
</div>
</body>
</html>
```